Folded A4 flyer for design&construction company

Folded A4 flyer needed. Keywords: elegant, stylish
our website www.dorvika.ae

Industry/Entity Type

Construction

```html
<!DOCTYPE html>
<html lang="en">
<head>
<meta charset="utf-8">
<title>Dorvika – Folded Flyer</title>
<link href="https://fonts.googleapis.com/css2?family=Lato:wght@300;400;700&display=swap" rel="stylesheet">
<style>
  :root {
    --bg: #e8e6e3;
    --paper: #ffffff;
    --ink: #1c1c1c;
    --soft-ink: #b8b8b8;
    --gold: #d4aa40;
    --grey: #bcbcbe;
    --lime: #c6d82c;
    --cyan: #00b6ec;
    --pink: #e35ba5;
    --yellow: #fdc31c;
    --magenta: #c7269a;
    --green: #2f8a3a;
  }
  * { margin: 0; padding: 0; box-sizing: border-box; }
  html, body { width: 800px; height: 1200px; overflow: hidden; }
  body { background: var(--bg); font-family: "Lato", sans-serif; color: var(--ink); position: relative; }

  .sheet { position: absolute; left: 20px; width: 760px; height: 538px; background: var(--paper); overflow: hidden; }
  .sheet--outside { top: 40px; }
  .sheet--inside { top: 622px; }

  .abs { position: absolute; }

  /* brand name block */
  .brand { position: absolute; display: flex; flex-direction: column; align-items: center; transform: translateX(-50%); }
  .brand__mark { width: 8px; height: 8px; background: var(--gold); margin-bottom: 6px; }
  .brand__name { font-family: "Lato", sans-serif; font-weight: 400; color: var(--ink); line-height: 1; letter-spacing: 0.5px; }

  /* outside: back panel */
  .intro { left: 78px; top: 155px; width: 225px; font-size: 9.6px; font-weight: 300; line-height: 13px; color: var(--soft-ink); text-align: justify; }
  .photo-strip { left: 0; top: 303px; width: 380px; height: 75px; display: flex; }
  .photo-strip div { flex: 1; }
  .photo-strip .p1 { background: linear-gradient(135deg, #b78a4a, #e9d2a8 60%, #8a6a40); }
  .photo-strip .p2 { background: linear-gradient(135deg, #caa471, #5a3b24 55%, #d7b98a); }
  .photo-strip .p3 { background: linear-gradient(135deg, #f2eee6, #e0a84a 60%, #b8782f); }
  .contact-panel { left: 0; top: 378px; width: 380px; height: 160px; background: var(--grey); }
  .quote-box { left: 80px; top: 15px; width: 219px; height: 75px; background: var(--gold); border: 1.5px solid #f3e2b4; text-align: center; color: #fff; font-size: 9px; line-height: 13px; padding-top: 9px; }
  .quote-box strong { display: block; color: var(--ink); font-weight: 400; font-size: 12px; line-height: 16px; letter-spacing: 0.2px; }
  .footer-info { left: 0; width: 380px; text-align: center; color: #fff; font-size: 9px; }

  /* outside: cover */
  .cover-photo { left: 380px; top: 190px; width: 380px; height: 348px;
    background:
      radial-gradient(ellipse 45% 14% at 42% 80%, rgba(70,70,70,.75), rgba(70,70,70,0) 100%),
      linear-gradient(180deg, #ffffff 0%, #eeeeee 30%, #dcdcdc 55%, #e8e8e8 75%, #f4f4f4 100%); }
  .motto { left: 380px; top: 190px; width: 380px; text-align: center; font-weight: 300; font-size: 17px; letter-spacing: 3.6px; color: #4a4a4a; line-height: 25px; }
  .motto__by { display: block; font-size: 10.5px; letter-spacing: 0.5px; line-height: 20px; color: #777; }

  /* inside */
  .logo-cell { background: var(--paper); }
  .list-cell { font-size: 10.6px; font-weight: 300; color: var(--ink); }
  .list-cell ul { list-style: none; position: absolute; }
  .list-cell li { height: 16.6px; line-height: 16.6px; position: relative; white-space: nowrap; }
  .list--right { text-align: right; }
  .list--right li::after { content: ""; position: absolute; right: -27px; top: 8px; width: 19px; height: 1.5px; background: var(--ink); }
  .list--right.list--light li::after { background: #fff; }
  .list--left li::before { content: ""; position: absolute; left: -28px; top: 8px; width: 19px; height: 1.5px; background: var(--ink); }
  .list--left li.cont::before { display: none; }
  .list--light { color: #fff; }

  .band { font-size: 18px; font-weight: 400; line-height: 1; }
  .photo { position: absolute; }
</style>
</head>
<body>

<!-- Outside of the fold -->
<section class="sheet sheet--outside">
  <div class="brand" style="left:190px; top:62px;">
    <span class="brand__mark"></span>
    <span class="brand__name" style="font-size:31px;">DORVIKA</span>
  </div>

  <p class="abs intro">We believe in quality beginnings and flawless finishes. We are a team of creative designers and constructors with years of experience and expertise in providing complete interior design and construction services. Our unique designing prowess is complemented by our unflinching commitment to quality construction. Our team specializes in classic and contemporary high quality construction in Dubai for commercial and residential projects.</p>

  <div class="abs photo-strip">
    <div class="p1" role="img" aria-label="Photo of a bathroom with a jacuzzi tub and arched window"></div>
    <div class="p2" role="img" aria-label="Photo of a living room with wooden wall panelling and TV"></div>
    <div class="p3" role="img" aria-label="Photo of a bright lobby with a curved staircase"></div>
  </div>

  <div class="abs contact-panel">
    <div class="abs quote-box">
      <strong>GET A FREE QUOTE TODAY!</strong>
      800 – DORVIKA<br>OR<br>CONTACT@DORVIKA.AE
    </div>
    <p class="abs footer-info" style="top:108px;">www.dorvika.ae</p>
    <p class="abs footer-info" style="top:123px;">Dorvika LLC, Marlow Bay Tower, Office 1207, Business</p>
  </div>

  <div class="abs cover-photo" role="img" aria-label="Photo of a bright white living room with white sofas, a glass coffee table, a dark rug and flowers"></div>

  <div class="brand" style="left:570px; top:48px;">
    <span class="brand__mark" style="width:10px;height:10px;margin-bottom:10px;"></span>
    <span class="brand__name" style="font-size:46px;">DORVIKA</span>
  </div>

  <p class="abs motto" style="top:186px;">QUALITY IS NOT AN ACT,<br>IT IS A HABIT<span class="motto__by">- THERON VALE -</span></p>
</section>

<!-- Inside of the fold -->
<section class="sheet sheet--inside">
  <!-- Design services -->
  <div class="abs logo-cell" style="left:0;top:0;width:174px;height:83px;"></div>
  <div class="brand" style="left:112px; top:26px;">
    <span class="brand__mark" style="width:6px;height:6px;margin-bottom:5px;"></span>
    <span class="brand__name" style="font-size:21px;">DORVIKA</span>
  </div>
  <div class="abs list-cell" style="left:0;top:83px;width:174px;height:199px;background:var(--lime);">
    <ul class="list--right" style="right:29px;top:10px;">
      <li>Villas Interior Design</li>
      <li>Villas Exterior Design</li>
      <li>Landscape Design</li>
      <li>Retail Interior Design</li>
      <li>Office Interior Design</li>
      <li>Hospitality Interior Design</li>
      <li>Hotel Interior Design</li>
      <li>Hotel Exterior Design</li>
      <li>Restaurant Interior Design</li>
    </ul>
  </div>

  <div class="abs" style="left:174px;top:0;width:206px;height:51px;background:var(--lime);"></div>
  <span class="abs band" style="left:284px;top:29px;color:var(--magenta);">DESIGN</span>
  <div class="photo" style="left:174px;top:51px;width:206px;height:231px;background:linear-gradient(160deg,#f4f1ec 0%,#d9cfc4 45%,#f7f5f2 65%,#4a3326 100%);" role="img" aria-label="Photo of a bedroom with a white bed, sheer curtains and a pendant lamp"></div>

  <!-- Fitout services -->
  <div class="abs" style="left:380px;top:0;width:205px;height:51px;background:var(--cyan);"></div>
  <span class="abs band" style="left:407px;top:29px;color:var(--magenta);">FITOUT</span>
  <div class="photo" style="left:380px;top:51px;width:205px;height:231px;background:linear-gradient(180deg,#9a6a3e 0%,#b98452 45%,#e8d3aa 62%,#f1e4c8 100%);" role="img" aria-label="Photo of a room with wooden wall units, a TV and light wood flooring"></div>

  <div class="abs logo-cell" style="left:585px;top:0;width:175px;height:83px;"></div>
  <div class="brand" style="left:649px; top:26px;">
    <span class="brand__mark" style="width:6px;height:6px;margin-bottom:5px;"></span>
    <span class="brand__name" style="font-size:21px;">DORVIKA</span>
  </div>
  <div class="abs list-cell" style="left:585px;top:83px;width:175px;height:199px;background:var(--cyan);">
    <ul class="list--left" style="left:30px;top:10px;">
      <li>Development Approvals</li>
      <li>Flooring Solutions</li>
      <li>Partition</li>
      <li>Sealing Solutions</li>
      <li>MEP Works</li>
      <li>Civil Works</li>
      <li>Joinery</li>
      <li>Glass and Aluminium</li>
      <li class="cont">Works (subcontractor)</li>
    </ul>
  </div>

  <!-- Landscaping services -->
  <div class="abs logo-cell" style="left:0;top:282px;width:174px;height:67px;"></div>
  <div class="brand" style="left:112px; top:298px;">
    <span class="brand__mark" style="width:6px;height:6px;margin-bottom:5px;"></span>
    <span class="brand__name" style="font-size:21px;">DORVIKA</span>
  </div>
  <div class="abs list-cell" style="left:0;top:349px;width:174px;height:189px;background:var(--pink);">
    <ul class="list--right list--light" style="right:29px;top:12px;">
      <li>Soft Landscaping</li>
      <li>Irrigation Solutions</li>
      <li>Hard land Scaping</li>
      <li>External Lighting</li>
      <li>Swimming Pool &amp;</li>
      <li style="margin-right:0;">Water Features</li>
    </ul>
  </div>

  <div class="abs" style="left:174px;top:282px;width:206px;height:27px;background:var(--pink);"></div>
  <span class="abs band" style="left:174px;width:206px;text-align:center;top:287px;color:var(--yellow);">LANDSCAPING</span>
  <div class="photo" style="left:174px;top:309px;width:206px;height:229px;background:linear-gradient(160deg,#f3e4c4 0%,#d9b27a 45%,#f6efe2 70%,#c99a5c 100%);" role="img" aria-label="Photo of a bathroom with a corner tub and a decorative iron window"></div>

  <!-- Maintenance services -->
  <div class="abs" style="left:380px;top:282px;width:205px;height:27px;background:var(--yellow);"></div>
  <span class="abs band" style="left:399px;top:287px;color:var(--green);">MAINTAINCE</span>
  <div class="photo" style="left:380px;top:309px;width:205px;height:229px;background:linear-gradient(180deg,#e7dcc8 0%,#cdb89a 40%,#8a6a4c 60%,#6f6a66 100%);" role="img" aria-label="Photo of a bathroom with a glass shower, wooden vanity and tiled floor"></div>

  <div class="abs logo-cell" style="left:585px;top:282px;width:175px;height:67px;"></div>
  <div class="brand" style="left:649px; top:298px;">
    <span class="brand__mark" style="width:6px;height:6px;margin-bottom:5px;"></span>
    <span class="brand__name" style="font-size:21px;">DORVIKA</span>
  </div>
  <div class="abs list-cell" style="left:585px;top:349px;width:175px;height:189px;background:var(--yellow);">
    <ul class="list--left" style="left:30px;top:8px;">
      <li>AC Repair</li>
      <li>Plumber Services</li>
      <li>Electric Repair</li>
      <li>Carpentry Work</li>
      <li>Gypsum Ceiling</li>
      <li>Painting Services</li>
      <li>Cleaning Services</li>
      <li>Emergency Services</li>
    </ul>
  </div>
</section>

</body>
</html>
```